Business Card Design

Copper Wing Bus Charters, name was derived from the Yellow Tail jack (fish). We are a school bus charter service that offers supplemental bus transportation to district schools for field trips, school sporting events, etc. We also offer bus service to recreation centers during summer time for field trips.
Our business incorporates the color sea or royal blue, school bus yellow and a dark or charcoal gray. Its a copy of the fish's natural color scheme.

I am looking for a logo with the color scheme listed. I am looking for something modern and professional.

Target Market(s)

School Administrators, City employees

Industry/Entity Type

Recreation

Contact Information for Business Card

Copper Wing Bus Charters LLC
Safe Reliable Affordable
Dermot Halvorsenby, Owner
P.O.BOX 28671
St. Petersburg, Fl 33733
555-314-9827
www.ridecopperwing.example
ridecopperwing@mailbox.example

Requirements
Should not have
• pictures of fish or buses

```html
<!DOCTYPE html>
<html lang="en">
<head>
<meta charset="utf-8">
<title>Copper Wing Bus Charters – Business Card</title>
<link rel="stylesheet" href="https://fonts.googleapis.com/css2?family=Cinzel:wght@400&family=Open+Sans:wght@400;600&display=swap">
<style>
  :root {
    --backdrop: #e4e6e8;
    --card: #ffffff;
    --card-shade: #eeeeee;
    --charcoal: #36393d;
    --brand-blue: #11aee8;
    --bus-yellow: #f7c51e;
  }
  html, body {
    margin: 0;
    width: 1200px;
    height: 675px;
    overflow: hidden;
    background: var(--backdrop);
  }
  .canvas {
    width: 1200px;
    height: 675px;
    display: flex;
    align-items: center;
    justify-content: center;
  }
  .business-card {
    position: relative;
    width: 980px;
    height: 560px;
    background: radial-gradient(ellipse at 40% 35%, var(--card) 0%, var(--card) 45%, var(--card-shade) 100%);
    box-shadow: 0 10px 30px rgba(0,0,0,0.18);
  }
  .holder {
    position: absolute;
    left: 560px;
    top: 70px;
    font-family: "Cinzel", serif;
    color: var(--charcoal);
  }
  .holder-name {
    margin: 0;
    font-size: 32px;
    font-weight: 400;
    letter-spacing: 0.5px;
    white-space: nowrap;
  }
  .holder-title {
    margin: 14px 0 0 14px;
    font-size: 32px;
    font-weight: 400;
  }
  .contact-list {
    position: absolute;
    left: 520px;
    top: 265px;
    margin: 0;
    padding: 0;
    list-style: none;
    font-family: "Open Sans", sans-serif;
    font-size: 20px;
    color: var(--charcoal);
    text-transform: uppercase;
    line-height: 1.35;
    white-space: nowrap;
  }
  .contact-item {
    position: relative;
    padding-left: 30px;
    margin-bottom: 10px;
  }
  .contact-item::before {
    content: "";
    position: absolute;
    left: 0;
    top: 6px;
    width: 16px;
    height: 16px;
    border-radius: 50%;
    background: var(--bus-yellow);
    border: 1px solid var(--charcoal);
  }
  .brand {
    position: absolute;
    left: 70px;
    bottom: 110px;
    font-family: "Open Sans", sans-serif;
    font-weight: 600;
    color: var(--brand-blue);
    text-transform: uppercase;
  }
  .brand-name {
    display: block;
    font-size: 46px;
    letter-spacing: 4px;
    line-height: 1;
  }
  .brand-sub {
    display: block;
    font-size: 25px;
    letter-spacing: 5px;
    margin-top: 4px;
    padding-left: 16px;
  }
  .tagline {
    position: absolute;
    left: 86px;
    bottom: 70px;
    margin: 0;
    font-family: "Open Sans", sans-serif;
    font-size: 17px;
    font-weight: 400;
    letter-spacing: 3px;
    text-transform: uppercase;
    color: var(--charcoal);
  }
  .tagline-dot {
    display: inline-block;
    width: 8px;
    height: 8px;
    margin: 0 10px 2px;
    border-radius: 50%;
    background: var(--bus-yellow);
  }
</style>
</head>
<body>
<main class="canvas">
  <article class="business-card">
    <header class="holder">
      <h1 class="holder-name">Dermot Halvorsenby</h1>
      <p class="holder-title">Owner</p>
    </header>

    <ul class="contact-list">
      <li class="contact-item">P.O.Box 28671<br>St. Petersburg, FL 33733</li>
      <li class="contact-item">555-314-9827</li>
      <li class="contact-item">ridecopperwing@mailbox.example</li>
      <li class="contact-item">www.ridecopperwing.example</li>
    </ul>

    <div class="brand">
      <span class="brand-name">Copper Wing</span>
      <span class="brand-sub">Bus Charters LLC</span>
    </div>
    <p class="tagline">Safe<span class="tagline-dot"></span>Reliable<span class="tagline-dot"></span>Affordable</p>
  </article>
</main>
</body>
</html>
```